Vorelan.com Personal Trainer/Fitness Website

I want a website to market my personal training/Outdoor Bootcamp Class services, as well as to ditribute nutrivex. I need a logo as well I included an address for the Harbor Gales 1975 logo. I'd like Vorelan in place of Harbor Gales, and in Black and white, just different enough so I can't get sued by the PBL.
https://www.pictofind.example/imgres?imgurl=http%3A%2F%2Fwww.darnell-quibury.example%2Fwp-content%2Fuploads%2F2014%2F01%2Fgales_logo4.jpg&imgrefurl=http%3A%2F%2Fwww.darnell-quibury.example%2Fpbl-logo-redesigns-harbor-gales%2F&docid=_qkwzR7TBAgXpL&tbnid=m4tpU8KdOXjnRP%3A&w=600&h=450&client=ms-android-carrier&bih=512&biw=360&ved=0ahUKEwiRtpgyp9HMAhUTwGMKHRPMBWMQMwg6KBQwFA&iact=mrc&uact=8.
It should be about 5 pages 1. home 2. about 3. Services 4. Blog/Videos and programs 5. Contact.
http://www.dorvinfitness.example.uk/ is a website I like the style of.

Target Market(s)

Seattle area

Industry/Entity Type

Fitness

Coding

Coded - Design and coding required

Number of Pages Required

4 page

Font styles to use
Serif
Sans Serif

Requirements
Must have
• A minimal look
Nice to have
• A logo similar to the 1975 Harbor Galewinds Logo, with a Small Milo Brandt ripping his shirt open(with a picture of the logo on his shirt, picture within picture) to turn into Ironjaw in the center. Skyline is black, Background and small figure white(with black logo on shirt)

```html
<!DOCTYPE html>
<html lang="en">
<head>
<meta charset="utf-8">
<title>Vorelan – Personal Training</title>
<link href="https://fonts.googleapis.com/css2?family=Lato:wght@400;700;900&family=Questrial&display=swap" rel="stylesheet">
<style>
:root{
  --red:#b52a2c;
  --red-deep:#9e2325;
  --ink:#222;
  --dark:#2b2a2a;
  --slate:#4a4a4a;
  --white:#fff;
  --muted:#666;
  --rule:#bbb;
}
*{margin:0;padding:0;box-sizing:border-box}
html,body{width:1200px;height:3309px;overflow:hidden}
body{font-family:"Lato",sans-serif;color:var(--ink);background:var(--white);position:relative}
.abs{position:absolute}
.heading{font-family:"Questrial",sans-serif;font-weight:400}
.center{text-align:center}

/* top bar */
.topbar{top:0;left:0;width:1200px;height:115px;background:var(--dark)}
.contact-line{left:132px;color:#fff;font-size:20px;display:flex;align-items:center;gap:14px}
.ring{width:32px;height:32px;border:2px solid var(--red);border-radius:50%;display:flex;align-items:center;justify-content:center}
.socials{top:14px;right:130px;display:flex;gap:14px}
.socials span{width:18px;height:18px;background:var(--red);border-radius:3px;display:block}
.trainer-btn{left:821px;top:57px;width:247px;height:47px;background:var(--red);color:#fff;border-radius:6px;font-weight:700;font-size:21px;display:flex;align-items:center;justify-content:center;gap:14px}
.trainer-btn i{width:30px;height:22px;background:#fff;border-radius:4px;display:block}

/* nav */
.nav{top:115px;left:0;width:1200px;height:44px;background:#fff}
.nav a{position:absolute;top:0;height:44px;line-height:44px;font-size:17px;color:#222;text-decoration:none;transform:translateX(-50%)}
.nav a.active{background:var(--red);color:#fff;width:108px;text-align:center}
.brand{left:504px;top:0;width:192px;height:159px;background:#fff;border-radius:0 0 96px 96px;display:flex;flex-direction:column;align-items:center;justify-content:center;gap:12px}
.brand-dot{width:70px;height:70px;border-radius:50%;background:var(--dark)}
.brand-name{font-family:"Lato",sans-serif;font-weight:900;font-size:32px;color:var(--ink);letter-spacing:1px}

/* hero */
.hero{top:159px;left:0;width:1200px;height:397px;background:linear-gradient(90deg,#1a1a1a,#2a2a2a 55%,#161616)}
.hero-photo{left:0;top:0;width:600px;height:397px;background:radial-gradient(ellipse at 50% 45%,#9a6a4c 0%,#6b4530 35%,#2a2a2a 75%)}
.hero-title{left:710px;top:166px;color:#fff;font-size:32px;line-height:43px;letter-spacing:1px;white-space:nowrap}
.btn-red{background:var(--red);color:#fff;font-weight:700;border-radius:6px;display:flex;align-items:center;justify-content:center;gap:12px;border:2px solid #fff}
.hero-btn{left:710px;top:273px;width:245px;height:45px;font-size:21px}
.arrow-circ{width:42px;height:42px;border:2px solid #fff;border-radius:50%;display:flex;align-items:center;justify-content:center}

/* services */
.services{top:556px;left:0;width:1200px;height:514px;background:var(--red)}
.services-bg{left:320px;top:0;width:560px;height:514px;background:radial-gradient(ellipse at 50% 40%,rgba(220,120,110,.35),rgba(181,42,44,0) 70%)}
.sec-title{font-size:34px;width:100%;text-align:center}
.rule{height:1px;background:currentColor;opacity:.7}
.rule-mark{height:4px;width:72px;background:var(--ink)}
.services p,.services h3,.services a{color:#fff}
.svc-icon{width:116px;height:116px;border-radius:50%;background:#1e1e1e;border:3px solid #fff}
.svc-name{font-size:24px;font-weight:700;width:320px;text-align:center}
.svc-text{font-size:17px;line-height:25px;width:320px;text-align:center}
.read-more{font-size:13px;font-weight:700;text-decoration:underline}

/* about */
.about{top:1070px;left:0;width:1200px;height:441px;background:#2e2d2d}
.about-scene{left:560px;top:0;width:640px;height:441px;background:linear-gradient(100deg,rgba(46,45,45,1) 0%,rgba(70,68,62,.9) 35%,rgba(110,105,85,.85) 100%);clip-path:polygon(18% 0,100% 0,100% 100%,0 100%)}
.about-title{left:137px;top:24px;color:#fff;font-size:34px}
.portrait{left:132px;top:130px;width:248px;height:245px;background:linear-gradient(160deg,#c9d4da,#7a8a92);border:2px solid #fff}
.about-head{left:426px;top:143px;font-size:28px;color:#fff}
.about-head em{font-style:normal;color:#d23a3c}
.about-text{left:426px;top:192px;width:540px;color:#fff;font-size:14.5px;line-height:20px}

/* programs */
.programs-title{top:1550px;left:0;font-size:32px}
.cal{left:132px;top:1632px;width:252px;height:254px;background:#fff;box-shadow:0 2px 6px rgba(0,0,0,.25);font-size:15px}
.cal-head{height:36px;background:var(--red);color:#fff;display:flex;align-items:center;justify-content:space-between;font-weight:700;font-size:21px}
.cal-head span.nav-btn{width:22px;height:36px;background:#1e1e1e;display:flex;align-items:center;justify-content:center}
.cal table{width:100%;border-collapse:collapse;text-align:center}
.cal th{font-size:11px;font-weight:400;color:#444;height:22px}
.cal td{height:34px;border:1px solid #ddd;font-size:16px}
.cal td.on{background:#111;color:#fff}
.event{left:437px;width:640px}
.date-box{position:absolute;left:0;top:0;width:52px;height:58px;border:2px solid var(--red);text-align:center;color:var(--red)}
.date-box b{display:block;background:var(--red);color:#fff;font-size:20px;height:30px;line-height:30px}
.date-box span{font-size:17px;line-height:24px}
.ev-title{position:absolute;left:72px;top:0;font-weight:700;font-size:17px}
.ev-text{position:absolute;left:72px;top:26px;font-size:14px;color:#333}
.ev-time{position:absolute;left:72px;top:48px;font-size:13px;color:#555;display:flex;gap:8px;align-items:center}

/* amenities */
.amenities{top:1930px;left:0;width:1200px;height:437px;background:linear-gradient(180deg,#2a2724,#3b3732 50%,#24211f)}
.amen-title{top:86px;width:100%;text-align:center;color:#fff;font-size:56px;letter-spacing:1px}
.amen-title mark{background:var(--red);color:#fff;padding:0 10px}
.amen-sub{top:172px;width:100%;text-align:center;color:#fff;font-size:19px;font-weight:700}
.play{left:565px;top:214px;width:70px;height:70px;border-radius:50%;background:#111;border:3px solid #fff;display:flex;align-items:center;justify-content:center}
.watch-btn{left:529px;top:305px;width:144px;height:44px;border-radius:6px;font-size:19px;font-weight:400;border:none}

/* testimonials */
.test-title{top:2406px;left:0;font-size:32px}
.test-title span{color:var(--red)}
.quote{width:76px;height:76px;border-radius:50%;background:#1e1e1e;border:3px solid var(--red);display:flex;align-items:center;justify-content:center;color:var(--red);font-size:48px;font-weight:900;line-height:1}
.quote-text{width:340px;font-size:13px;line-height:19px;color:#222}
.quote-text b{color:var(--red);font-weight:400}
.quote-name{color:var(--red);font-size:15px}
.side-arrow{width:40px;height:40px;border-radius:50%;display:flex;align-items:center;justify-content:center}

/* contact */
.started{top:2746px;left:0;width:1200px;height:259px;background:var(--slate);color:#fff}
.ci{display:flex;align-items:center;gap:18px;font-size:18px}
.ci .ring{border-color:#fff;width:44px;height:44px}
.form-band{top:3005px;left:0;width:1200px;height:255px;background:var(--red);color:#fff}
.notch{left:565px;top:3005px;width:0;height:0;border-left:22px solid transparent;border-right:22px solid transparent;border-top:20px solid var(--slate)}
.field{background:#fff;color:#444;font-size:13px;padding:8px 10px;height:36px}
.send{background:#1e1e1e;color:#fff;font-size:18px;display:flex;align-items:center;justify-content:center;letter-spacing:1px}
.footer{top:3260px;left:0;width:1200px;height:49px;background:#2b2a2a;color:#bbb;font-size:12px}
</style>
</head>
<body>

<header class="abs topbar">
  <div class="abs contact-line" style="top:16px">
    <span class="ring"><svg width="16" height="16" viewBox="0 0 24 24"><path fill="#b52a2c" d="M6.6 10.8a15 15 0 0 0 6.6 6.6l2.2-2.2a1 1 0 0 1 1-.25 11 11 0 0 0 3.6.6 1 1 0 0 1 1 1V20a1 1 0 0 1-1 1A17 17 0 0 1 3 4a1 1 0 0 1 1-1h3.5a1 1 0 0 1 1 1c0 1.25.2 2.45.6 3.6a1 1 0 0 1-.25 1z"/></svg></span>
    014.276.5830
  </div>
  <div class="abs contact-line" style="top:62px">
    <span class="ring"><svg width="16" height="12" viewBox="0 0 24 18"><rect x="1" y="1" width="22" height="16" rx="2" fill="#b52a2c"/><path d="M2 2l10 8 10-8" stroke="#fff" stroke-width="2" fill="none"/></svg></span>
    info@vorelan.com
  </div>
  <div class="abs socials"><span></span><span></span><span></span><span></span></div>
  <div class="abs trainer-btn"><i></i>FIND A TRAINER</div>
</header>

<nav class="abs nav">
  <a class="active" style="left:158px">HOME</a>
  <a style="left:280px">ABOUT US</a>
  <a style="left:417px">SERVICES</a>
  <a style="left:757px">BLOG</a>
  <a style="left:882px">PROGRAMS</a>
  <a style="left:1026px">CONTACT</a>
</nav>
<div class="abs brand">
  <span class="brand-dot"></span>
  <span class="brand-name">VORELAN</span>
</div>

<section class="abs hero">
  <div class="abs hero-photo" role="img" aria-label="Muscular trainer, bare torso, against a dark background"></div>
  <div class="abs arrow-circ" style="left:29px;top:178px"><svg width="12" height="14" viewBox="0 0 12 14"><path d="M9 1L3 7l6 6" stroke="#fff" stroke-width="2" fill="none"/></svg></div>
  <div class="abs arrow-circ" style="left:1102px;top:178px"><svg width="12" height="14" viewBox="0 0 12 14"><path d="M3 1l6 6-6 6" stroke="#fff" stroke-width="2" fill="none"/></svg></div>
  <h1 class="abs heading hero-title">GET FIT &amp; HAVE FUN<br>THE WAY IT SHOULD BE</h1>
  <div class="abs btn-red hero-btn">
    <svg width="20" height="20" viewBox="0 0 24 24"><path fill="#fff" d="M6.6 10.8a15 15 0 0 0 6.6 6.6l2.2-2.2a1 1 0 0 1 1-.25 11 11 0 0 0 3.6.6 1 1 0 0 1 1 1V20a1 1 0 0 1-1 1A17 17 0 0 1 3 4a1 1 0 0 1 1-1h3.5a1 1 0 0 1 1 1c0 1.25.2 2.45.6 3.6a1 1 0 0 1-.25 1z"/></svg>
    CONTACT NOW
  </div>
</section>

<section class="abs services">
  <div class="abs services-bg" role="img" aria-label="Faint athlete silhouette behind the services"></div>
  <h2 class="abs heading sec-title" style="top:30px;color:#fff">OUR SERVICES</h2>
  <div class="abs rule" style="left:145px;top:90px;width:910px;color:#fff"></div>
  <div class="abs rule-mark" style="left:564px;top:88px"></div>
  <p class="abs center" style="left:190px;top:113px;width:820px;font-size:16px;line-height:28px">Lorem ipsum dolor sit amet, consectetur adipiscing elit. Morbi quis ante sed massa consectetur feugiat id at tellus. Fusce tristique dictum tincidunt. Nam viverra euismod pretium</p>

  <div class="abs svc-icon" style="left:209px;top:191px"></div>
  <div class="abs svc-icon" style="left:542px;top:191px"></div>
  <div class="abs svc-icon" style="left:877px;top:191px"></div>

  <h3 class="abs svc-name" style="left:107px;top:325px">Personal Training</h3>
  <h3 class="abs svc-name" style="left:440px;top:325px">Online Coaching</h3>
  <h3 class="abs svc-name" style="left:775px;top:325px">Outdoor Bootcamp</h3>
  <p class="abs svc-text" style="left:107px;top:355px">Lorem ipsum dolor sit amet,<br>consectetur adipiscing elit.<br>Morbi quis ante sed.</p>
  <p class="abs svc-text" style="left:440px;top:355px">Lorem ipsum dolor sit amet,<br>consectetur adipiscing elit.<br>Morbi quis ante sed.</p>
  <p class="abs svc-text" style="left:775px;top:355px">Lorem ipsum dolor sit amet,<br>consectetur adipiscing elit.<br>Morbi quis ante sed.</p>
  <a class="abs read-more" style="left:226px;top:448px">Read More</a>
  <a class="abs read-more" style="left:559px;top:448px">Read More</a>
  <a class="abs read-more" style="left:894px;top:448px">Read More</a>
</section>

<section class="abs about">
  <div class="abs about-scene" role="img" aria-label="Outdoor bootcamp group exercising on grass"></div>
  <h2 class="abs heading about-title">About Us</h2>
  <div class="abs" style="left:132px;top:84px;width:580px;height:1px;background:#d23a3c"></div>
  <div class="abs" style="left:132px;top:82px;width:150px;height:3px;background:#fff"></div>
  <div class="abs portrait" role="img" aria-label="Portrait of the personal trainer"></div>
  <h3 class="abs heading about-head"><em>Motivation, Consistency</em> &amp; Intensity</h3>
  <p class="abs about-text">Lorem ipsum dolor sit amet, consectetur adipiscing elit. Sed vitae magna tellus. Aenean ante nunc, semper nec cursus non, rutrum ac eros. Vestibulum mattis justo ac dui bibendum consequat a ac ipsum. Praesent a arcu venenatis, auctor velit eu, suscipit libero. Quisque convallis, leo ac pharetra sagittis, ipsum arcu auctor urna, sit amet cursus risus augue in eros. Duis lacinia nisi vitae leo commodo, non finibus magna maximus. Sed posuere, neque eget bibendum pulvinar, ligula erat suscipit dolor, ut maximus arcu mi et tortor. Quisque imperdiet turpis et ligula mollis ultricies. Mauris lacinia rhoncus odio, at rutrum diam mollis eu.</p>
</section>

<h2 class="abs heading sec-title programs-title">Our Programs</h2>
<div class="abs rule" style="left:132px;top:1604px;width:936px;color:#999"></div>
<div class="abs rule-mark" style="left:564px;top:1602px"></div>

<div class="abs cal">
  <div class="cal-head">
    <span class="nav-btn" style="background:var(--red-deep)"><svg width="8" height="12" viewBox="0 0 8 12"><path d="M7 1L2 6l5 5" stroke="#fff" stroke-width="2" fill="none"/></svg></span>
    MAY 2016
    <span class="nav-btn"><svg width="8" height="12" viewBox="0 0 8 12"><path d="M1 1l5 5-5 5" stroke="#fff" stroke-width="2" fill="none"/></svg></span>
  </div>
  <table>
    <tr><th>SUN</th><th>MON</th><th>TUE</th><th>WED</th><th>THU</th><th>FRI</th><th>SAT</th></tr>
    <tr><td></td><td>1</td><td class="on">2</td><td>3</td><td>4</td><td>5</td><td>6</td></tr>
    <tr><td>7</td><td>8</td><td>9</td><td>10</td><td>11</td><td class="on">12</td><td>13</td></tr>
    <tr><td>14</td><td>15</td><td class="on">16</td><td>17</td><td>18</td><td>19</td><td>20</td></tr>
    <tr><td>21</td><td>22</td><td>23</td><td>24</td><td>25</td><td>26</td><td>27</td></tr>
    <tr><td>28</td><td>29</td><td>30</td><td>31</td><td></td><td></td><td></td></tr>
  </table>
</div>

<div class="abs event" style="top:1636px;height:70px">
  <div class="date-box"><b>02</b><span>MAY</span></div>
  <div class="ev-title">Lorem ipsum dolor sit amet, consectetur adipiscing</div>
  <div class="ev-text">Lorem ipsum dolor sit amet, consectetur adipiscing elit. Sed vitae magna tellus.</div>
  <div class="ev-time"><svg width="12" height="12" viewBox="0 0 12 12"><circle cx="6" cy="6" r="5" stroke="#555" fill="none"/><path d="M6 3v3h2" stroke="#555" fill="none"/></svg>07:00 am</div>
</div>
<div class="abs event" style="top:1721px;height:70px">
  <div class="date-box"><b>12</b><span>MAY</span></div>
  <div class="ev-title">Lorem ipsum dolor sit amet, consectetur adipiscing</div>
  <div class="ev-text">Lorem ipsum dolor sit amet, consectetur adipiscing elit. Sed vitae magna tellus.</div>
  <div class="ev-time"><svg width="12" height="12" viewBox="0 0 12 12"><circle cx="6" cy="6" r="5" stroke="#555" fill="none"/><path d="M6 3v3h2" stroke="#555" fill="none"/></svg>08:00 am</div>
</div>
<div class="abs event" style="top:1805px;height:70px">
  <div class="date-box"><b>16</b><span>MAY</span></div>
  <div class="ev-title">Lorem ipsum dolor sit amet, consectetur adipiscing</div>
  <div class="ev-text">Lorem ipsum dolor sit amet, consectetur adipiscing elit. Sed vitae magna tellus.</div>
  <div class="ev-time"><svg width="12" height="12" viewBox="0 0 12 12"><circle cx="6" cy="6" r="5" stroke="#555" fill="none"/><path d="M6 3v3h2" stroke="#555" fill="none"/></svg>07:30 am</div>
</div>

<section class="abs amenities" role="img" aria-label="Dimly lit gym floor with weight machines">
  <h2 class="abs heading amen-title">STATE OF THE ART <mark>AMENITIES</mark></h2>
  <p class="abs amen-sub">LOREM IPSUM DOLOR SIT AMET CONSECTETUR ADIPISCING ELIT SED VITAE MAGNA TELLUS</p>
  <div class="abs play"><svg width="22" height="24" viewBox="0 0 22 24"><path d="M3 2l17 10L3 22z" fill="#fff"/></svg></div>
  <div class="abs btn-red watch-btn">Watch Video</div>
</section>

<h2 class="abs heading sec-title test-title">CLIENT <span>TESTIMONIALS</span></h2>
<div class="abs rule" style="left:132px;top:2460px;width:936px;color:#999"></div>
<div class="abs rule-mark" style="left:564px;top:2458px"></div>

<div class="abs side-arrow" style="left:50px;top:2577px;border:1px solid #ccc"><svg width="10" height="14" viewBox="0 0 10 14"><path d="M8 1L2 7l6 6" stroke="#aaa" stroke-width="2" fill="none"/></svg></div>
<div class="abs side-arrow" style="left:1110px;top:2577px;background:#2b2a2a"><svg width="10" height="14" viewBox="0 0 10 14"><path d="M2 1l6 6-6 6" stroke="#fff" stroke-width="2" fill="none"/></svg></div>

<div class="abs quote" style="left:130px;top:2494px">&ldquo;</div>
<p class="abs quote-text" style="left:225px;top:2486px">Lorem ipsum dolor sit amet, consectetur adipiscing elit. Sed vitae magna tellus. Aenean ante nunc, semper nec cursus non, rutrum ac eros. Vestibulum mattis justo... <b>Read More</b></p>
<p class="abs quote-name" style="left:225px;top:2554px">Renata Holm Ashby</p>

<div class="abs quote" style="left:630px;top:2494px">&ldquo;</div>
<p class="abs quote-text" style="left:730px;top:2486px">Lorem ipsum dolor sit amet, consectetur adipiscing elit. Sed vitae magna tellus. Aenean ante nunc, semper nec cursus non, rutrum ac eros. Vestibulum mattis justo... <b>Read More</b></p>
<p class="abs quote-name" style="left:730px;top:2554px">Dana Pruitt</p>

<div class="abs quote" style="left:130px;top:2616px">&ldquo;</div>
<p class="abs quote-text" style="left:225px;top:2616px">Lorem ipsum dolor sit amet, consectetur adipiscing elit. Sed vitae magna tellus. Aenean ante nunc, semper nec cursus non, rutrum ac eros. Vestibulum mattis justo... <b>Read More</b></p>
<p class="abs quote-name" style="left:225px;top:2682px">Marcus</p>

<div class="abs quote" style="left:630px;top:2616px">&ldquo;</div>
<p class="abs quote-text" style="left:730px;top:2616px">Lorem ipsum dolor sit amet, consectetur adipiscing elit. Sed vitae magna tellus. Aenean ante nunc, semper nec cursus non, rutrum ac eros. Vestibulum mattis justo... <b>Read More</b></p>
<p class="abs quote-name" style="left:730px;top:2682px">Owen</p>

<section class="abs started">
  <h2 class="abs heading sec-title" style="top:30px;font-size:31px">LET'S GET STARTED</h2>
  <div class="abs rule" style="left:132px;top:87px;width:936px;color:#aaa"></div>
  <p class="abs center heading" style="top:110px;width:100%;font-size:22px">Thank you for your interest in contacting VORELAN</p>
  <div class="abs ci" style="left:227px;top:165px">
    <span class="ring"><svg width="16" height="20" viewBox="0 0 16 20"><path d="M8 1a6 6 0 0 0-6 6c0 5 6 12 6 12s6-7 6-12a6 6 0 0 0-6-6z" fill="#fff"/><circle cx="8" cy="7" r="2.2" fill="#4a4a4a"/></svg></span>
    <span style="font-size:17px;line-height:22px">Lorem ipsum dolor sit<br>amet - 12345</span>
  </div>
  <div class="abs ci" style="left:556px;top:165px">
    <span class="ring"><svg width="18" height="18" viewBox="0 0 24 24"><path fill="#fff" d="M6.6 10.8a15 15 0 0 0 6.6 6.6l2.2-2.2a1 1 0 0 1 1-.25 11 11 0 0 0 3.6.6 1 1 0 0 1 1 1V20a1 1 0 0 1-1 1A17 17 0 0 1 3 4a1 1 0 0 1 1-1h3.5a1 1 0 0 1 1 1c0 1.25.2 2.45.6 3.6a1 1 0 0 1-.25 1z"/></svg></span>
    014.276.5830
  </div>
  <div class="abs ci" style="left:783px;top:165px">
    <span class="ring"><svg width="18" height="14" viewBox="0 0 24 18"><rect x="1" y="1" width="22" height="16" rx="2" fill="#fff"/><path d="M2 2l10 8 10-8" stroke="#4a4a4a" stroke-width="2" fill="none"/></svg></span>
    info@vorelan.com
  </div>
</section>

<section class="abs form-band">
  <h2 class="abs heading sec-title" style="top:36px;font-size:25px">Please Fill Out The Form Below</h2>
  <div class="abs field" style="left:141px;top:94px;width:294px">Your Name</div>
  <div class="abs field" style="left:452px;top:94px;width:296px">Email</div>
  <div class="abs field" style="left:765px;top:94px;width:294px">Phone</div>
  <div class="abs field" style="left:141px;top:141px;width:607px;height:73px">Comments</div>
  <div class="abs send" style="left:765px;top:143px;width:144px;height:35px">SEND</div>
</section>
<div class="abs notch"></div>

<footer class="abs footer">
  <p class="abs" style="left:132px;top:18px">Copyright © 2016 VORELAN. All Rights Reserved.</p>
  <div class="abs" style="right:130px;top:15px;display:flex;gap:14px">
    <span style="width:18px;height:18px;background:#999;border-radius:3px;display:block"></span>
    <span style="width:18px;height:18px;background:#999;border-radius:3px;display:block"></span>
    <span style="width:18px;height:18px;background:#999;border-radius:3px;display:block"></span>
    <span style="width:18px;height:18px;background:#999;border-radius:3px;display:block"></span>
  </div>
</footer>

</body>
</html>
```